Professional & attention grabbing.

A business card design, front and back. I already have a logo I will attach, but I am open to something new as well.
Things to include:
Name:
Title:
Phone:
Email:
Wanting something that is professional but attention grabbing.
Also we do a lot of work using drones on natural gas pipelines (leading the future)if you want to include any of that. I'm open to ideas.
Target Market(s)
Natural gas transmission industry / greenhouse gas mitigation industry
Industry/Entity Type
Business
Colors
Designer to choose colors to be used in the design.
Look and feel
Each slider illustrates characteristics of the customer's brand and the style your logo design should communicate.

```html
<!DOCTYPE html>
<html lang="en">
<head>
<meta charset="utf-8">
<title>Veyra Inspections – Business Card</title>
<link rel="stylesheet" href="https://fonts.googleapis.com/css2?family=Open+Sans:ital,wght@0,400;0,600;0,700;1,400&display=swap">
<style>
  :root {
    --backdrop: #5a4a3c;
    --charcoal: #38383b;
    --signal-red: #c11f24;
    --paper: #ffffff;
    --ink: #3a3a3a;
    --muted: #555555;
  }
  * { margin: 0; padding: 0; box-sizing: border-box; }
  html, body {
    width: 1200px; height: 987px; overflow: hidden;
    background: var(--backdrop);
    font-family: "Open Sans", Arial, sans-serif;
  }
  .card {
    position: absolute;
    left: 293px;
    width: 615px;
    height: 352px;
    box-shadow: 0 2px 6px rgba(0,0,0,0.35);
  }
  .card--front { top: 130px; display: flex; background: var(--paper); }
  .card--back { top: 506px; background: var(--signal-red); }

  .front-brand {
    width: 312px; height: 100%;
    background: var(--charcoal);
    display: flex; align-items: center; justify-content: center;
  }
  .front-details { flex: 1; position: relative; padding: 68px 0 0 48px; }
  .front-edge {
    position: absolute; right: 0; top: 0;
    width: 15px; height: 100%; background: var(--signal-red);
  }

  .wordmark {
    display: flex; align-items: center; gap: 10px;
    color: var(--paper); font-weight: 700; letter-spacing: 0.5px;
  }
  .wordmark__square { display: block; background: var(--signal-red); }
  .front-brand .wordmark { font-size: 26px; }
  .front-brand .wordmark__square { width: 22px; height: 22px; }

  .person-name {
    color: var(--signal-red); font-weight: 600; font-size: 21px; line-height: 1.1;
  }
  .person-title { color: var(--ink); font-size: 17px; margin-top: 4px; }
  .contact-list { list-style: none; margin-top: 22px; }
  .contact-list li {
    display: flex; align-items: center; gap: 8px;
    color: var(--muted); font-size: 16px; line-height: 24px;
  }
  .contact-list svg { width: 14px; height: 14px; fill: var(--signal-red); flex: none; }

  .back-brand {
    position: absolute; left: 0; right: 0; top: 146px;
    display: flex; justify-content: center;
  }
  .back-brand .wordmark { font-size: 44px; gap: 14px; }
  .back-brand .wordmark__square { width: 36px; height: 36px; background: var(--paper); }
  .back-web {
    position: absolute; left: 0; right: 0; top: 290px;
    text-align: center; color: var(--paper);
    font-style: italic; font-size: 15px; letter-spacing: 4px;
  }
</style>
</head>
<body>
  <section class="card card--front">
    <div class="front-brand">
      <div class="wordmark"><span class="wordmark__square"></span>Veyra Inspections</div>
    </div>
    <div class="front-details">
      <p class="person-name">DANA WHITLOCK</p>
      <p class="person-title">CEO/Founder</p>
      <ul class="contact-list">
        <li>
          <svg viewBox="0 0 16 16" aria-hidden="true"><path d="M3.5 1l3 3-1.8 1.8c.9 2 2.5 3.6 4.5 4.5L11 8.5l3 3-2 2.5C6.5 14 2 9.5 1 3.5z"/></svg>
          555 014 2290
        </li>
        <li>
          <svg viewBox="0 0 16 16" aria-hidden="true"><path d="M1 3h14v10H1z M1.8 3.8L8 8.5l6.2-4.7" stroke="#fff" stroke-width="1.2"/></svg>
          hello@veyrainspect.com
        </li>
        <li>
          <svg viewBox="0 0 16 16" aria-hidden="true"><circle cx="8" cy="8" r="7"/><path d="M1 8h14M8 1c-3 3.5-3 10.5 0 14M8 1c3 3.5 3 10.5 0 14" stroke="#fff" stroke-width="1" fill="none"/></svg>
          www.veyrainspect.com
        </li>
      </ul>
      <div class="front-edge"></div>
    </div>
  </section>

  <section class="card card--back">
    <div class="back-brand">
      <div class="wordmark"><span class="wordmark__square"></span>Veyra Inspections</div>
    </div>
    <p class="back-web">www.veyrainspect.com</p>
  </section>
</body>
</html>
```